Gearhead Rally 5, The fifth annual Gearhead Rally motorcycle event, www.gearheadrally.example

We need an event poster that can be used in print and on the web to promote our event. Files for the poster should be modifiable to add additional information as it becomes available. The Gearhead Rally is a gathering for Vintage, Classic and Cafe' Racer motorcycles and their riders, Rockers and Mods. The event date is Saturday, July 26, 2014, rain or shine, from 9:00 AM to 6:00 PM EDT at Maplewick Park, 217 North Birch Avenue, Alderbrook, NY 18651 USA. Friday July 25 Meet and Greet from 7:00 PM to close at Hadley's Hideaway, Alderbrook, NY. Early Birds' Brunch, Sunday, July 27, 7:00 to 10:00 AM, location tba. Optional Group Ride Saturday from 10:00 AM to Noon. Tarvex 450 Custom Cafe' Motorcycle Raffle, Contests, Trophies and Cash Prizes for Pin-up Girl, Coolest Cafe' Racer Motorcycle, Coolest Mod Scooter, Peoples Choice Motorcycle, and More! Live music by the one and only legendary KLTV, "Slim Jim" Varga and more tba. Brought to you by Wyland Throttlers, www.social.example/wylandthrottlers?ref=hl, Bixby and Moss/Moss Rascals, www.bixbyandmoss.example. Partial Proceeds to benefit the UFWL and The Valley Rescue Volunteers Society. More information and advance tickets available at www.gearheadrally.example
Uploaded files include: Wyland Throttlers Logo, Moss Rascal's Logo, stock vintage image, two images from 2014 event, and a photo of the bike to be raffled (better image in the works.

Thank you to all who participated in our competition.  We received excellent work from you all, and the hard part for us is having to choose.  Our decision will be made today.

```html
<!DOCTYPE html>
<html lang="en">
<head>
<meta charset="utf-8">
<title>Gearhead Rally 5 — Event Poster</title>
<link rel="stylesheet" href="https://fonts.googleapis.com/css2?family=Montserrat:wght@600;700&family=Oswald:wght@500;600&display=swap">
<style>
  :root {
    --poster-red: #c8161c;
    --poster-red-deep: #9e0f14;
    --poster-red-bright: #e0262a;
    --ink: #0b0b0b;
    --paper: #ffffff;
    --banner-navy: #262a63;
    --bike-light: #b9b9b9;
    --bike-mid: #6e6e6e;
    --bike-dark: #1c1c1c;
  }
  html, body {
    margin: 0;
    padding: 0;
    width: 1200px;
    height: 1000px;
    overflow: hidden;
    background: var(--paper);
  }
  .poster {
    position: relative;
    width: 1200px;
    height: 1000px;
    overflow: hidden;
    background:
      radial-gradient(ellipse at 30% 35%, var(--poster-red-bright) 0%, transparent 55%),
      radial-gradient(ellipse at 80% 70%, var(--poster-red-bright) 0%, transparent 50%),
      linear-gradient(180deg, var(--poster-red-deep) 0%, var(--poster-red) 45%, var(--poster-red) 100%);
  }
  .poster-art {
    position: absolute;
    inset: 0;
    width: 1200px;
    height: 1000px;
  }
  .headline-kicker {
    font-family: "Montserrat", sans-serif;
    font-weight: 700;
    fill: var(--ink);
  }
  .headline-name,
  .headline-word {
    font-family: "Montserrat", sans-serif;
    font-weight: 600;
    fill: var(--paper);
  }
  .tagline-band { fill: var(--banner-navy); }
  .tagline-text {
    font-family: "Oswald", sans-serif;
    font-weight: 600;
    font-size: 30px;
    fill: var(--paper);
  }
  .event-date {
    font-family: "Montserrat", sans-serif;
    font-weight: 600;
    fill: var(--paper);
  }
  .footer-bar { fill: var(--ink); }
  .footer-text {
    font-family: "Oswald", sans-serif;
    font-weight: 500;
    font-size: 19px;
    fill: var(--paper);
  }
</style>
</head>
<body>
<main class="poster">
  <svg class="poster-art" viewBox="0 0 1200 1000" xmlns="http://www.w3.org/2000/svg">
    <defs>
      <linearGradient id="bike-tone" x1="0" y1="0" x2="0" y2="1">
        <stop offset="0" stop-color="var(--bike-light)"/>
        <stop offset="0.55" stop-color="var(--bike-mid)"/>
        <stop offset="1" stop-color="var(--bike-dark)"/>
      </linearGradient>
    </defs>

    <text class="headline-kicker" x="30" y="96" font-size="104" textLength="1145" lengthAdjust="spacingAndGlyphs">THE FIFTH ANNUAL</text>
    <text class="headline-name" x="25" y="318" font-size="252" textLength="1155" lengthAdjust="spacingAndGlyphs">GEARHEAD</text>
    <text class="headline-word" x="30" y="706" font-size="512" textLength="1150" lengthAdjust="spacingAndGlyphs">RALLY</text>

    <g class="tagline" transform="translate(602 494) rotate(-14.2)">
      <rect class="tagline-band" x="-600" y="-27" width="1200" height="54"/>
      <text class="tagline-text" x="0" y="11" text-anchor="middle" textLength="1140" lengthAdjust="spacing">VINTAGE, CLASSIC AND CAFÉ RACER MOTORCYCLES AND THEIR RIDERS</text>
    </g>

    <path class="bike-photo" role="img" aria-label="Halftone photograph of a café racer motorcycle in side view"
      fill="url(#bike-tone)"
      d="M40 945 C45 870 110 820 200 815 L250 700 C270 640 320 605 360 600 L420 610 L470 660 C560 650 700 655 760 670 L900 690 C960 700 1040 700 1060 730 L1080 760 C1140 790 1170 860 1175 945 Z"/>

    <text class="event-date" x="700" y="785" font-size="70" textLength="475" lengthAdjust="spacingAndGlyphs">JULY 26 2014</text>

    <rect class="footer-bar" x="0" y="945" width="1200" height="55"/>
    <text class="footer-text" x="22" y="980" textLength="1156" lengthAdjust="spacing">RAIN OR SHINE. 09:00 AM TO 06:00 PM EDT AT MAPLEWICK PARK, 217 NORTH BIRCH AVENUE, ALDERBROOK, NY 18651 USA</text>
  </svg>
</main>
</body>
</html>
```